Contemporary new French wine brand needs logo and series of label design

to design a new contemporary logo and series of labels for a new French wine brand. We hope to attract not just current French wine drinkers but new ones who may appreciate a less traditional and more modern style.
Updates

Reason: we are wanting to extend the project for a few days more to receive more submissions since we had fewer designs submitted than we were expecting, maybe because of the holidays.

Target Market(s)

people who follow the arts community (eg. music, theatre, visual/video arts, dance) --- all mature ages.

Industry/Entity Type

French Wine

Requirements
Must have
• a clear, memorable treatment for the name MORIVAL with accompanying logo.
Nice to have
• embossing, matte/gloss refinement, tasteful foil stamping, coated stock for the whites to help the integrity of the paper in and out of ice buckets. A combo of say, three types of fonts; a semi custom font for the brand name Morival and maybe a script and one other.
Should not have
• not traditional French

```html
<!DOCTYPE html>
<html lang="fr">
<head>
<meta charset="utf-8">
<title>Morival — Val de Loire Sauvignon Blanc</title>
<link rel="stylesheet" href="https://fonts.googleapis.com/css2?family=Libre+Caslon+Text:wght@400;700&family=Pinyon+Script&display=swap">
<style>
  :root {
    --backdrop: #ececec;
    --label-light: #f0efdc;
    --label-mid: #e3e1c9;
    --label-edge: #cfcdb4;
    --ink: #2e2a25;
    --ink-soft: #4a443c;
    --sketch-light: #c9c5ad;
    --sketch-dark: #8e877a;
    --gold: #a8862e;
  }
  * { margin: 0; padding: 0; box-sizing: border-box; }
  html, body {
    width: 748px;
    height: 1200px;
    overflow: hidden;
    background: var(--backdrop);
  }
  .canvas {
    position: relative;
    width: 748px;
    height: 1200px;
  }
  .label {
    position: absolute;
    left: 44px;
    top: 403px;
    width: 660px;
    height: 394px;
    background: linear-gradient(90deg, var(--label-edge) 0%, var(--label-mid) 12%, var(--label-light) 45%, var(--label-mid) 85%, var(--label-edge) 100%);
  }
  .estate-sketch {
    position: absolute;
    left: 109px;
    top: 37px;
    width: 450px;
    height: 107px;
    background: linear-gradient(180deg, var(--label-light) 0%, var(--sketch-light) 55%, var(--sketch-dark) 100%);
    opacity: 0.7;
  }
  .brand-name {
    position: absolute;
    left: 0;
    width: 100%;
    top: 158px;
    text-align: center;
    font-family: "Libre Caslon Text", serif;
    font-weight: 700;
    font-size: 54px;
    letter-spacing: 4px;
    color: var(--ink);
    line-height: 1;
  }
  .vintage {
    position: absolute;
    left: 0;
    width: 100%;
    top: 240px;
    text-align: center;
    font-family: "Libre Caslon Text", serif;
    font-size: 22px;
    color: var(--ink-soft);
    line-height: 1;
  }
  .vine-mark {
    position: absolute;
    left: 284px;
    top: 276px;
    width: 126px;
    height: 48px;
    background: radial-gradient(ellipse at 55% 50%, var(--sketch-dark) 0%, var(--label-mid) 75%);
    opacity: 0.8;
  }
  .region {
    position: absolute;
    left: 110px;
    top: 328px;
    font-family: "Pinyon Script", cursive;
    font-size: 32px;
    color: var(--ink-soft);
    line-height: 1;
  }
  .varietal {
    position: absolute;
    left: 0;
    width: 100%;
    top: 366px;
    padding-left: 40px;
    text-align: center;
    font-family: "Libre Caslon Text", serif;
    font-weight: 700;
    font-size: 18px;
    letter-spacing: 1.5px;
    color: var(--gold);
    line-height: 1;
  }
</style>
</head>
<body>
  <main class="canvas">
    <section class="label">
      <div class="estate-sketch" role="img" aria-label="Pen sketch of the estate house among trees on a vineyard hillside"></div>
      <h1 class="brand-name">MORIVAL</h1>
      <p class="vintage">2009</p>
      <div class="vine-mark" role="img" aria-label="Small ink sketch of a vine stock"></div>
      <p class="region">Val de Loire</p>
      <p class="varietal">SAUVIGNON BLANC</p>
    </section>
  </main>
</body>
</html>
```